Automotive eCommerce Business looking for a business card design

Looking for a clean and simple business card design. Our company name is "Brindle Auto" and we are a company specializing in the ecommerce sales of automotive parts, specifically for pick up trucks and large SUVs. Our company colours are red, black, and white.

Feel free to use the logo provided or create a new logo that you seem fit. Looking forward to your creative ideas!

Industry/Entity Type

Automotive

Contact Information for Business Card

We were thinking of a possibly two-sided design featuring just the logo and company name on one side, and personal information on the other side. Single sided designs will be considered as well.

Font styles to use
Serif
Sans Serif
Decorative

Colors
ec1f27
ffffff
000000

Requirements
Must have
• Space for employee's name, title, phone number and email address, along with the company address and website somewhere.

```html
<!DOCTYPE html>
<html lang="en">
<head>
<meta charset="UTF-8">
<title>Brindle Auto Ltd – Business Card</title>
<link rel="stylesheet" href="https://fonts.googleapis.com/css2?family=Cinzel:wght@500&family=Open+Sans:wght@400;700&display=swap">
<style>
  :root {
    --brand-red: #a31c23;
    --ink: #1a1a1a;
    --ink-soft: #333333;
    --paper: #fbfbfb;
    --backdrop: #ececec;
    --serif: "Cinzel", Georgia, serif;
    --sans: "Open Sans", Arial, sans-serif;
  }
  * { box-sizing: border-box; margin: 0; padding: 0; }
  html, body {
    width: 1200px; height: 900px; overflow: hidden;
    background: var(--backdrop);
  }
  .stage {
    position: relative; width: 1200px; height: 900px;
    display: flex; align-items: center; justify-content: center; gap: 40px;
  }
  .card {
    position: relative; width: 540px; height: 309px;
    box-shadow: 0 2px 6px rgba(0,0,0,0.12);
  }
  /* Details side */
  .card--details { background: var(--paper); }
  .person { position: absolute; left: 34px; top: 30px; }
  .person__name {
    font: 700 17px/1.1 var(--sans); color: var(--brand-red);
    letter-spacing: 0.5px; text-transform: uppercase;
  }
  .person__title { font: 400 12px/1.4 var(--sans); color: var(--ink-soft); }
  .contacts { position: absolute; left: 34px; top: 126px; list-style: none; }
  .contacts li {
    display: flex; align-items: center; gap: 8px;
    font: 400 12.5px/1.75 var(--sans); color: var(--ink);
  }
  .contacts svg { width: 10px; height: 10px; fill: var(--brand-red); flex: none; }
  .wordmark {
    display: flex; align-items: center; gap: 12px;
    font: 500 25px/1 var(--serif); letter-spacing: 1px; white-space: nowrap;
  }
  .wordmark__square { width: 22px; height: 22px; flex: none; }
  .card--details .wordmark {
    position: absolute; right: 34px; top: 140px; color: var(--ink);
  }
  .card--details .wordmark__square { background: var(--brand-red); }
  .address {
    position: absolute; right: 34px; bottom: 30px; text-align: right;
    font: 400 12px/1.5 var(--sans); color: var(--ink-soft);
  }
  /* Brand side */
  .card--brand {
    background: var(--brand-red);
    display: flex; align-items: center; justify-content: center;
  }
  .card--brand .wordmark { color: #ffffff; font-size: 28px; }
  .card--brand .wordmark__square { background: #ffffff; width: 26px; height: 26px; }
</style>
</head>
<body>
<main class="stage">
  <section class="card card--details" aria-label="Business card, contact side">
    <div class="person">
      <p class="person__name">Marcus Hale</p>
      <p class="person__title">Managing Director</p>
    </div>
    <ul class="contacts">
      <li>
        <svg viewBox="0 0 10 10" aria-hidden="true"><path d="M2 0.5 L3.6 2.6 L2.8 3.6 C3.5 5 4.8 6.4 6.3 7.1 L7.3 6.3 L9.5 7.9 L8.3 9.5 C4.4 9.2 0.7 5.5 0.5 1.7 Z"/></svg>
        (044)987654321
      </li>
      <li>
        <svg viewBox="0 0 10 10" aria-hidden="true"><path d="M0.5 2 H9.5 V8 H0.5 Z M0.5 2 L5 5.5 L9.5 2" stroke="#fbfbfb" stroke-width="0.7"/></svg>
        info@brindleauto.com
      </li>
      <li>
        <svg viewBox="0 0 10 10" aria-hidden="true"><circle cx="5" cy="5" r="4.5"/><path d="M0.5 5 H9.5 M5 0.5 C3 3 3 7 5 9.5 M5 0.5 C7 3 7 7 5 9.5" stroke="#fbfbfb" stroke-width="0.6" fill="none"/></svg>
        www.brindleauto.com
      </li>
    </ul>
    <div class="wordmark">
      <span class="wordmark__square" aria-hidden="true"></span>
      <span class="wordmark__name">Brindle Auto Ltd</span>
    </div>
    <p class="address">58, Harrow Lane, Kent,<br>United Kingdom, 4521</p>
  </section>

  <section class="card card--brand" aria-label="Business card, brand side">
    <div class="wordmark">
      <span class="wordmark__square" aria-hidden="true"></span>
      <span class="wordmark__name">Brindle Auto Ltd</span>
    </div>
  </section>
</main>
</body>
</html>
```